redesign of my existing custom website into Wordpress based website

I need someone to redesign my current website into something more classy, simplistic, modern and on trend. I would like it set up on Wordpress in a way thats easy for me to make my own additions to blogs/price changes and promotion banners. I will also need a page that is password protected so members can login and have access to all my training videos and resources.
website is www.tidewellmamas.com.au

Target Market(s)

new mums

Industry/Entity Type

Fitness

Coding

Coded - Design and coding required

Number of Pages Required

5+ page

Colors
33a6d7

Requirements
Must have
• chic, modern, stylish and simplistic.
• a call to action above the page fold
• mobile friendly conversion
• a pop up message as soon as someone enters my sight offering my free report
• a members page that is password protected containing 3 youtube videos and 6 pdf attachments as resources
• a home page
• a contact us page
• an about us page
• a blog page
• a store page
Nice to have
• some examples of my peers websites that I like:
• www.norapellwick.com
• https://www.9qlr.com
• https://41bytedgarth.com
Should not have
• anything gimmicky

```html
<!DOCTYPE html>
<html lang="en">
<head>
<meta charset="utf-8">
<title>Tidewell Mamas – Home Fitness</title>
<link rel="stylesheet" href="https://fonts.googleapis.com/css2?family=Nunito+Sans:wght@400;600;700;800&family=Open+Sans:wght@400;600&display=swap">
<style>
:root{
  --blue:#33a6d7;
  --blue-deep:#1f7fc4;
  --pink:#e0217f;
  --ink:#2b2b2b;
  --muted:#6b6b6b;
  --grey-bg:#efefef;
  --light-bg:#f6f6f6;
  --white:#ffffff;
}
*{box-sizing:border-box;margin:0;padding:0}
html,body{width:1200px;height:3614px;overflow:hidden}
body{font-family:"Open Sans",Arial,sans-serif;color:var(--ink);background:var(--white);position:relative}
.heading{font-family:"Nunito Sans",Arial,sans-serif}
section,header,footer{position:absolute;left:0;width:1200px}
.btn{display:inline-block;background:var(--blue);color:var(--white);font-family:"Nunito Sans",Arial,sans-serif;font-weight:700;text-align:center}
.ticks{list-style:none}
.ticks li{display:flex;align-items:center;gap:12px;font-size:15px;color:#444;margin-bottom:14px}
.ticks svg{flex:none}

/* header */
.site-header{top:0;height:101px;background:var(--white)}
.brand{position:absolute;left:150px;top:28px;display:flex;align-items:center;gap:12px}
.brand-dot{width:44px;height:44px;border-radius:50%;background:var(--pink)}
.brand-name{font-family:"Nunito Sans",Arial,sans-serif;font-weight:700;font-size:24px;color:var(--pink)}
.main-nav{position:absolute;left:0;top:0;width:1200px;height:101px}
.main-nav a{position:absolute;top:0;font-family:"Nunito Sans",Arial,sans-serif;font-size:17px;color:#9a9a9a;text-decoration:none;line-height:101px;white-space:nowrap}
.main-nav a.active{color:var(--ink);font-weight:700}
.main-nav a.active::after{content:"";position:absolute;left:-8px;right:-8px;bottom:0;height:5px;background:var(--blue)}
.cart{position:absolute;left:968px;top:28px;width:44px;height:44px;border-radius:50%;background:var(--pink);display:flex;align-items:center;justify-content:center}

/* hero */
.hero{top:101px;height:557px;background:linear-gradient(120deg,#8e8a88 0%,#4a4544 45%,#2f2b2c 100%);text-align:center;color:var(--white)}
.hero-play{position:absolute;left:557px;top:198px}
.hero-title{position:absolute;top:300px;left:0;width:100%;font-weight:800;text-transform:uppercase;line-height:1.15}
.hero-title .l1{font-size:34px;display:block}
.hero-title .l2{font-size:46px;display:block}
.hero .btn{position:absolute;left:499px;top:400px;width:183px;height:53px;line-height:53px;font-size:15px;text-transform:uppercase}

/* about */
.about{top:658px;height:450px;background:linear-gradient(90deg,#ffffff 45%,#f4f4f4 70%,#ececec 100%)}
.about-visual{position:absolute;right:0;top:0;width:520px;height:450px;background:radial-gradient(circle at 60% 55%,#f1d6dd 0%,#f3eaec 35%,rgba(240,240,240,0) 70%)}
.about h2{position:absolute;left:150px;top:96px;font-size:34px;font-weight:600;color:var(--ink)}
.about p{position:absolute;left:150px;top:152px;width:500px;font-size:14px;line-height:1.55;color:var(--muted)}
.about .ticks{position:absolute;left:150px;top:216px}
.signup{position:absolute;left:720px;top:82px;width:317px;height:296px;background:var(--blue);text-align:center;padding:34px 28px 0}
.signup h3{color:var(--white);font-size:18px;font-weight:700;text-transform:uppercase;white-space:nowrap}
.signup h4{color:var(--white);font-size:21px;font-weight:700;margin-top:6px;white-space:nowrap}
.signup .field{height:38px;background:var(--white);margin-top:12px;text-align:left;padding-left:12px;line-height:38px;font-size:13px;color:#aaa}
.signup .field:first-of-type{margin-top:20px}
.signup .submit{height:52px;background:#2d2d2d;color:var(--white);line-height:52px;font-size:19px;margin-top:12px}

/* basic pack */
.basic{top:1108px;height:434px;background:var(--light-bg)}
.basic-photo{position:absolute;left:0;top:0;width:640px;height:434px;background:linear-gradient(100deg,#cfc8bd 0%,#e8e3dc 55%,#f6f6f6 100%)}
.basic h2{position:absolute;left:656px;top:82px;font-size:30px;font-weight:600;line-height:1.2;color:var(--ink)}
.basic .ticks{position:absolute;left:656px;top:180px}
.outline-btn{position:absolute;left:661px;top:326px;width:126px;height:36px;border:2px solid var(--blue);color:var(--blue);font-size:14px;text-align:center;line-height:32px}

/* included */
.included{top:1566px;height:482px;background:linear-gradient(180deg,#3d3939 0%,#5a5250 55%,#2d2a2b 100%);color:var(--white);text-align:center}
.included h2{position:absolute;top:112px;width:100%;font-size:38px;font-weight:700}
.included p{position:absolute;left:230px;top:170px;width:740px;font-size:17px;line-height:1.6}
.included .btn{position:absolute;left:526px;top:272px;width:136px;height:38px;line-height:38px;font-size:15px}

/* results */
.results{top:2048px;height:482px;background:linear-gradient(180deg,var(--blue) 0%,var(--blue-deep) 100%)}
.results h2{position:absolute;top:42px;width:100%;text-align:center;color:var(--white);font-size:31px;font-weight:700}
.result-card{position:absolute;top:111px;width:282px;height:328px;background:var(--white);text-align:center}
.result-photo{height:214px;background:linear-gradient(180deg,#eeeeee,#d9d6d2)}
.lost{position:absolute;left:50%;top:140px;margin-left:-46px;width:92px;height:92px;border-radius:50%;background:var(--blue-deep);color:var(--white);font-family:"Nunito Sans",Arial,sans-serif;padding-top:18px;line-height:1}
.lost small{font-size:14px;display:block;margin-bottom:2px}
.lost b{font-size:30px}
.lost b span{font-size:15px}
.result-card h3{position:absolute;left:0;top:230px;width:100%;color:var(--blue);font-size:28px;font-weight:600;line-height:1.1}
.result-card p{position:absolute;left:22px;top:268px;width:238px;font-size:11px;line-height:1.5;color:#555}

/* why */
.why{top:2530px;height:405px;background:var(--white)}
.why h2{position:absolute;top:42px;width:100%;text-align:center;color:var(--blue);font-size:31px;font-weight:600}
.why-tile{position:absolute;top:121px;width:285px;height:236px;border-radius:8px;display:flex;flex-direction:column;align-items:center;justify-content:center;color:var(--white);text-align:center;font-family:"Nunito Sans",Arial,sans-serif;font-size:18px;font-weight:600;text-transform:uppercase;line-height:1.35;gap:10px}
.tile-mums{left:152px;background:linear-gradient(135deg,#6a5a52,#2f2826)}
.tile-equip{left:455px;background:linear-gradient(135deg,#f3dde4,#e8e8ea);color:#555}
.tile-recipes{left:759px;background:var(--blue)}

/* news */
.news{top:2935px;height:330px;background:var(--grey-bg)}
.news h2{position:absolute;left:147px;top:52px;color:var(--blue);font-size:29px;font-weight:400}
.news-arrows{position:absolute;left:956px;top:56px;display:flex;gap:10px}
.news-arrows span{width:26px;height:26px;border-radius:50%;background:#c9c9c9;display:flex;align-items:center;justify-content:center}
.post{position:absolute;top:120px;width:270px}
.post h3{font-size:19px;font-weight:600;line-height:1.35;color:var(--ink)}
.post p{margin-top:12px;font-size:11.5px;line-height:1.6;color:#666}

/* footer */
.site-footer{top:3265px;height:349px;background:var(--white)}
.foot-col{position:absolute;top:56px}
.foot-col h4{font-family:"Nunito Sans",Arial,sans-serif;font-size:17px;font-weight:600;text-transform:uppercase;color:var(--ink);margin-bottom:12px}
.foot-col a{display:block;font-size:14px;color:#777;text-decoration:none;line-height:31px}
.socials{display:flex;gap:8px}
.socials span{width:28px;height:28px;border-radius:50%;border:2px solid var(--blue)}
.foot-brand{display:flex;align-items:center;gap:10px;margin-top:24px}
.foot-brand .brand-dot{width:40px;height:40px}
.foot-brand .brand-name{font-size:21px}
.foot-rule{position:absolute;left:158px;top:287px;width:884px;height:1px;background:#d6d6d6}
.copyright{position:absolute;top:305px;width:100%;text-align:center;font-size:12px;color:#888}
</style>
</head>
<body>

<header class="site-header">
  <div class="brand"><span class="brand-dot"></span><span class="brand-name">Tidewell Mamas</span></div>
  <nav class="main-nav">
    <a class="active" href="#" style="left:429px">Home</a>
    <a href="#" style="left:508px">About Us</a>
    <a href="#" style="left:612px">Program</a>
    <a href="#" style="left:711px">Blog</a>
    <a href="#" style="left:776px">Shop</a>
    <a href="#" style="left:848px">Contact Us</a>
  </nav>
  <div class="cart">
    <svg width="20" height="18" viewBox="0 0 20 18"><path d="M2 6h16l-2 11H4z" fill="#fff"/><path d="M6 6a4 4 0 0 1 8 0" stroke="#fff" stroke-width="2" fill="none"/></svg>
  </div>
</header>

<section class="hero" role="img" aria-label="Photo of a mum working out at home beside her smiling baby">
  <svg class="hero-play" width="86" height="86" viewBox="0 0 86 86"><circle cx="43" cy="43" r="40" fill="none" stroke="#fff" stroke-width="3"/><path d="M35 27l24 16-24 16z" fill="#fff"/></svg>
  <h1 class="hero-title heading"><span class="l1">Lose your baby weight and</span><span class="l2">Bounce back into shape</span></h1>
  <a class="btn">Call to action</a>
</section>

<section class="about">
  <div class="about-visual" role="img" aria-label="Pink dumbbells, trainers and an apple on a white floor"></div>
  <h2 class="heading">About Tidewell Mamas</h2>
  <p>Class aptent taciti sociosqu ad litora torquent per conubia nostra per inceptos hymenaeos Proin nulla arcu nonummy luctus dictum eget</p>
  <ul class="ticks">
    <li><svg width="16" height="16"><circle cx="8" cy="8" r="8" fill="var(--blue)"/><path d="M4.5 8.2l2.3 2.3 4.7-4.7" stroke="#fff" stroke-width="1.8" fill="none"/></svg>12 week, cardio and resistance circuit training program</li>
    <li><svg width="16" height="16"><circle cx="8" cy="8" r="8" fill="var(--blue)"/><path d="M4.5 8.2l2.3 2.3 4.7-4.7" stroke="#fff" stroke-width="1.8" fill="none"/></svg>Triple workout DVDWorkout equipment delivered to your front door</li>
    <li><svg width="16" height="16"><circle cx="8" cy="8" r="8" fill="var(--blue)"/><path d="M4.5 8.2l2.3 2.3 4.7-4.7" stroke="#fff" stroke-width="1.8" fill="none"/></svg>Weekly coaching emails</li>
    <li><svg width="16" height="16"><circle cx="8" cy="8" r="8" fill="var(--blue)"/><path d="M4.5 8.2l2.3 2.3 4.7-4.7" stroke="#fff" stroke-width="1.8" fill="none"/></svg>Accountability charts &amp; program cards</li>
  </ul>
  <div class="signup heading">
    <h3>Get your free top 10</h3>
    <h4>Baby Belly Blasting Tips</h4>
    <div class="field">Name</div>
    <div class="field">Email address</div>
    <div class="submit">Get it Free Now!</div>
  </div>
</section>

<section class="basic">
  <div class="basic-photo" role="img" aria-label="Photo of a mum and toddler playing with dumbbells on a yoga mat"></div>
  <h2 class="heading">12 week Home Workout<br>Program - Basic Pack</h2>
  <ul class="ticks">
    <li><svg width="16" height="16"><circle cx="8" cy="8" r="8" fill="var(--blue)"/><path d="M4.5 8.2l2.3 2.3 4.7-4.7" stroke="#fff" stroke-width="1.8" fill="none"/></svg>Our 3 stage, 12 week training program</li>
    <li><svg width="16" height="16"><circle cx="8" cy="8" r="8" fill="var(--blue)"/><path d="M4.5 8.2l2.3 2.3 4.7-4.7" stroke="#fff" stroke-width="1.8" fill="none"/></svg>Full Instructional Workout DVD for each program</li>
    <li><svg width="16" height="16"><circle cx="8" cy="8" r="8" fill="var(--blue)"/><path d="M4.5 8.2l2.3 2.3 4.7-4.7" stroke="#fff" stroke-width="1.8" fill="none"/></svg>Weekly accountability charts</li>
    <li><svg width="16" height="16"><circle cx="8" cy="8" r="8" fill="var(--blue)"/><path d="M4.5 8.2l2.3 2.3 4.7-4.7" stroke="#fff" stroke-width="1.8" fill="none"/></svg>Weekly coaching emails</li>
  </ul>
  <a class="outline-btn">Learn More</a>
</section>

<section class="included" role="img" aria-label="Photo of a mum doing sit-ups on a living room rug">
  <h2 class="heading">What's included in the Program?</h2>
  <p>Praesent elementum elit at tellus nec ultricies sit amet porttitor mattis enim In massa libero interdum nec interdum vel blandit sed nulla In ullamcorper est eget tempor cursus neque mi consectetuer mi a ultricies massa est sed nisl</p>
  <a class="btn">Learn More</a>
</section>

<section class="results">
  <h2 class="heading">Check Our Some Awesome Results</h2>
  <div class="result-card" style="left:159px">
    <div class="result-photo" role="img" aria-label="Before and after photos of a program member"></div>
    <div class="lost"><small>LOST</small><b>12<span>KG</span></b></div>
    <h3 class="heading">Marla</h3>
    <p>Lost 12 kgs and 25 cms in 12 weeks! After spending a lot of time researching the best post</p>
  </div>
  <div class="result-card" style="left:458px">
    <div class="result-photo" role="img" aria-label="Before and after photos of a program member"></div>
    <div class="lost"><small>LOST</small><b>10<span>KG</span></b></div>
    <h3 class="heading">KT</h3>
    <p>Lost 12 kgs and 25 cms in 12 weeks! After spending a lot of time researching the best post</p>
  </div>
  <div class="result-card" style="left:754px">
    <div class="result-photo" role="img" aria-label="Before and after photos of a program member"></div>
    <div class="lost"><small>LOST</small><b>8<span>KG</span></b></div>
    <h3 class="heading">Bev</h3>
    <p>Lost 12 kgs and 25 cms in 12 weeks! After spending a lot of time researching the best post</p>
  </div>
</section>

<section class="why">
  <h2 class="heading">Why Our Program is Different</h2>
  <div class="why-tile tile-mums" role="img" aria-label="Photo of a mum holding her baby">Specially designed<br>for mums<svg width="18" height="18" viewBox="0 0 18 18"><path d="M2 9h11M9 4l5 5-5 5" stroke="#fff" stroke-width="3" fill="none"/></svg></div>
  <div class="why-tile tile-equip" role="img" aria-label="Photo of workout equipment">Workout equipment<br>included<svg width="18" height="18" viewBox="0 0 18 18"><path d="M2 9h11M9 4l5 5-5 5" stroke="#555" stroke-width="3" fill="none"/></svg></div>
  <div class="why-tile tile-recipes" role="img" aria-label="Photo of healthy family food">Delicious low fat<br>family recipes<svg width="18" height="18" viewBox="0 0 18 18"><path d="M2 9h11M9 4l5 5-5 5" stroke="#fff" stroke-width="3" fill="none"/></svg></div>
</section>

<section class="news">
  <h2 class="heading">Latest News</h2>
  <div class="news-arrows">
    <span><svg width="10" height="10"><path d="M7 1L3 5l4 4" stroke="#fff" stroke-width="2" fill="none"/></svg></span>
    <span><svg width="10" height="10"><path d="M3 1l4 4-4 4" stroke="#fff" stroke-width="2" fill="none"/></svg></span>
  </div>
  <article class="post" style="left:147px">
    <h3 class="heading">The benefits of training in the morning</h3>
    <p>Class aptent taciti sociosqu ad litora torquent per conubia nostra per inceptos hymenaeos Proin nulla arcu nonummy luctus</p>
  </article>
  <article class="post" style="left:458px">
    <h3 class="heading">Marla's 10 exercise lounge room cardio workout</h3>
    <p>Class aptent taciti sociosqu ad litora torquent per conubia nostra per inceptos hymenaeos Proin nulla arcu nonummy luctus</p>
  </article>
  <article class="post" style="left:793px;width:225px">
    <h3 class="heading">Healthy Shepherds Pie Recipe</h3>
    <p>Class aptent taciti sociosqu ad litora torquent per conubia nostra per inceptos hymenaeos Proin nulla arcu nonummy luctus</p>
  </article>
</section>

<footer class="site-footer">
  <div class="foot-col" style="left:149px"><h4>Quick Links</h4><a>Home</a><a>About Us</a><a>Programs</a><a>Blog</a></div>
  <div class="foot-col" style="left:361px"><h4>Sublinks</h4><a>Term of Use</a><a>Privacy Policy</a><a>My Cart</a><a>Contact</a></div>
  <div class="foot-col" style="left:561px"><h4>Resources</h4><a>News</a><a>Join Now</a><a>Shop</a></div>
  <div class="foot-col" style="left:771px"><h4>Follow Us</h4>
    <div class="socials"><span></span><span></span><span></span><span></span></div>
    <div class="foot-brand"><span class="brand-dot"></span><span class="brand-name">Tidewell Mamas</span></div>
  </div>
  <div class="foot-rule"></div>
  <div class="copyright">© 2017 Company Name. All right reserved</div>
</footer>

</body>
</html>
```